Corporate Template

Looking for a set of corporate slides to be made which contain multiple different slides and orientations. Looking for at least 8 to 10 different master pages plus a Coversheet and closeout page. Incorporating a color palate similar to our logo coloring is preferred.
I have attached a logo.
I like the amber quill works designs best so far. They seem to fit what I'm looking for in terms of visual appearance.
Reason: I'm trying to allow time for a couple new designers to incorporate some changes I requested to their existing designs.

```html
<!DOCTYPE html>
<html lang="en">
<head>
<meta charset="utf-8">
<title>Our Team – Cortexa Labs</title>
<link rel="stylesheet" href="https://fonts.googleapis.com/css2?family=Ubuntu:wght@400;500;700&display=swap">
<style>
  :root {
    --brand-blue: #2f6dad;
    --brand-blue-deep: #285f9c;
    --brand-blue-light: #3d82c4;
    --accent-sky: #8cc6ff;
    --rule-sky: #6fb3f2;
    --name-blue: #1f5a96;
    --ink: #2b2b2b;
    --ink-soft: #333;
    --avatar-fill: #c9c9c9;
    --avatar-ring: #ececec;
    --white: #ffffff;
  }
  * { box-sizing: border-box; margin: 0; padding: 0; }
  html, body { width: 1200px; height: 900px; overflow: hidden; background: var(--white); }
  body { font-family: "Ubuntu", sans-serif; }
  .slide { position: relative; width: 1200px; height: 900px; overflow: hidden; background: var(--white); }

  .slide-header {
    position: absolute; left: 0; top: 0; width: 1200px; height: 90px;
    background: linear-gradient(90deg, var(--brand-blue-light), var(--brand-blue) 60%, var(--brand-blue-deep));
    border-bottom: 5px solid var(--rule-sky);
  }
  .slide-title {
    position: absolute; left: 24px; top: 22px;
    font-size: 39px; font-weight: 700; color: var(--accent-sky);
  }
  .header-mark {
    position: absolute; left: 1113px; top: 12px; width: 72px; height: 72px;
    border-radius: 50%; border: 3px solid var(--white);
  }

  .intro {
    position: absolute; left: 24px; top: 118px; width: 1070px;
    font-size: 19px; line-height: 34px; color: var(--ink-soft);
  }

  .team-divider {
    position: absolute; left: 636px; top: 203px; width: 2px; height: 510px;
    background: linear-gradient(180deg, rgba(180,150,150,0), rgba(150,110,110,0.5), rgba(180,150,150,0));
  }

  .member { position: absolute; top: 220px; width: 560px; text-align: center; }
  .member--left { left: 12px; }
  .member--right { left: 660px; }
  .member-photo {
    display: block; margin: 0 auto; width: 234px; height: 234px; border-radius: 50%;
    background: radial-gradient(circle at 50% 40%, #d2d2d2, var(--avatar-fill));
    border: 5px solid var(--avatar-ring);
    box-shadow: 0 0 4px rgba(0,0,0,0.12);
  }
  .member-name { margin-top: 10px; font-size: 29px; font-weight: 500; color: var(--name-blue); }
  .member-role { margin-top: 10px; font-size: 22px; font-weight: 500; color: var(--ink); }
  .member-bio { margin: 12px auto 0; width: 520px; font-size: 18.5px; line-height: 33px; color: var(--ink-soft); }

  .footer-wave { position: absolute; left: 0; top: 700px; }
  .brand-name {
    position: absolute; left: 30px; top: 808px;
    font-size: 40px; font-weight: 500; color: var(--white); letter-spacing: 1px;
  }
  .copyright { position: absolute; left: 787px; top: 864px; font-size: 20px; color: var(--accent-sky); }
  .page-number {
    position: absolute; left: 1146px; top: 833px; width: 38px; height: 38px; border-radius: 50%;
    background: var(--white); color: var(--brand-blue-deep);
    font-size: 16px; font-weight: 700; line-height: 38px; text-align: center;
  }
</style>
</head>
<body>
<main class="slide">
  <header class="slide-header">
    <h1 class="slide-title">Our Team</h1>
    <div class="header-mark"></div>
  </header>

  <p class="intro">Buesiness profile hereBuesiness profile here Buesiness profile hereBuesiness profile hereBuesiness profile hereBuesiness profile here Buesiness profile</p>

  <div class="team-divider"></div>

  <section class="member member--left">
    <div class="member-photo" role="img" aria-label="Portrait photo of the co-founder"></div>
    <h2 class="member-name">Founder Name</h2>
    <p class="member-role">Co-Founder</p>
    <p class="member-bio">Buesiness profile hereBuesiness profile hereBuesiness profile hereBuesiness profile hereBuesiness profile hereBuesiness profile hereBuesiness profile hereBuesiness profile hereBuesiness profile hereBuesiness profile here</p>
  </section>

  <section class="member member--right">
    <div class="member-photo" role="img" aria-label="Portrait photo of the co-founder"></div>
    <h2 class="member-name">Founder Name</h2>
    <p class="member-role">Co-Founder</p>
    <p class="member-bio">Buesiness profile hereBuesiness profile hereBuesiness profile hereBuesiness profile hereBuesiness profile hereBuesiness profile hereBuesiness profile hereBuesiness profile hereBuesiness profile hereBuesiness profile here</p>
  </section>

  <svg class="footer-wave" width="1200" height="200" viewBox="0 0 1200 200" aria-hidden="true">
    <defs>
      <linearGradient id="footerFill" x1="0" y1="0" x2="1" y2="0">
        <stop offset="0" stop-color="#2d68a8"/>
        <stop offset="0.6" stop-color="#3474b5"/>
        <stop offset="1" stop-color="#3d82c4"/>
      </linearGradient>
    </defs>
    <rect x="0" y="0" width="1200" height="200" fill="url(#footerFill)"/>
    <path d="M0,0 L0,36 C300,110 720,165 1200,25 L1200,0 Z" fill="#ffffff"/>
    <path d="M0,36 C300,110 720,165 1200,25" fill="none" stroke="#7dbcf5" stroke-width="4"/>
    <line x1="0" y1="152" x2="1200" y2="152" stroke="#5a97d4" stroke-width="1.5" opacity="0.6"/>
  </svg>

  <div class="brand-name">CORTEXA LABS</div>
  <p class="copyright">Copyright text here</p>
  <div class="page-number">01</div>
</main>
</body>
</html>
```